Bramwell IT Services Business Card

Bramwell IT Services are a Perth based IT Services company. We would like to incorporate our company logo (attached) and stick with the blue that is in that design. I would like a clean look design that isn't too busy, yet creates a lasting image that is instantly recognisable in the recipients mind.

Target Market(s)

The target audience is small/medium business owners.

Industry/Entity Type

Business

Font styles to use
Serif
Sans Serif

Colors

Designer to choose colors to be used in the design.

Requirements
Must have
• The design should include:
Business name: Bramwell IT Services
Directors Name: Marcus Tenley
Phone Number: 0483 562 904
Email: support@bramwellit.com.au
Website: www.bramwellit.com.au

```html
<!DOCTYPE html>
<html lang="en">
<head>
<meta charset="utf-8">
<title>Bramwell IT Services Business Card</title>
<link href="https://fonts.googleapis.com/css2?family=Mulish:wght@400;700;800&display=swap" rel="stylesheet">
<style>
  :root {
    --bg: #e6e8eb;
    --card: #f4f4f5;
    --brand-blue: #1f6fd1;
    --band-blue: #1593e6;
    --label-blue: #2a9be8;
    --accent-light: #3cc3f2;
    --accent-deep: #1a66d6;
    --ink: #3a3d42;
    --white: #ffffff;
  }
  * { margin: 0; padding: 0; box-sizing: border-box; }
  html, body {
    width: 1200px; height: 900px; overflow: hidden;
    background: var(--bg);
    font-family: "Mulish", sans-serif;
  }
  .canvas {
    width: 1200px; height: 900px;
    display: flex; flex-direction: column;
    align-items: center; justify-content: center; gap: 56px;
  }
  .card {
    position: relative;
    width: 620px; height: 379px;
    background: var(--card);
    box-shadow: 0 6px 20px rgba(0,0,0,0.12);
    overflow: hidden;
  }
  /* Wordmark */
  .wordmark { display: flex; align-items: center; gap: 12px; color: var(--brand-blue); font-weight: 800; }
  .wordmark__mark { width: 16px; height: 16px; background: var(--brand-blue); flex: none; }
  .wordmark__name { text-transform: uppercase; line-height: 1; letter-spacing: 0.02em; white-space: nowrap; }

  .card--back { display: flex; align-items: center; justify-content: center; }
  .card--back .wordmark__name { font-size: 30px; }

  /* Front: corner brand graphic area */
  .brand-graphic {
    position: absolute; left: 0; top: 0;
    width: 250px; height: 230px;
  }

  .card--front .wordmark { position: absolute; left: 262px; top: 72px; }
  .card--front .wordmark__name { font-size: 25px; }

  .name-band {
    position: absolute; left: 262px; right: 0; top: 148px; height: 48px;
    background: var(--band-blue);
    display: flex; align-items: center; padding-left: 22px;
  }
  .name-band__name { color: var(--white); font-weight: 700; font-size: 25px; white-space: nowrap; }

  .contacts {
    position: absolute; left: 222px; top: 220px;
    list-style: none; display: grid; gap: 10px;
  }
  .contacts__item { display: flex; align-items: baseline; gap: 28px; font-size: 17px; color: var(--ink); white-space: nowrap; }
  .contacts__label { width: 12px; color: var(--label-blue); font-weight: 700; font-size: 14px; }
</style>
</head>
<body>
  <main class="canvas">
    <section class="card card--back" aria-label="Card back">
      <div class="wordmark">
        <span class="wordmark__mark"></span>
        <span class="wordmark__name">Bramwell IT Services</span>
      </div>
    </section>

    <section class="card card--front" aria-label="Card front">
      <svg class="brand-graphic" viewBox="0 0 250 230" role="img" aria-label="Large blue brand graphic area">
        <defs>
          <linearGradient id="brandGraphicFill" x1="0" y1="1" x2="1" y2="0">
            <stop offset="0" stop-color="var(--accent-deep)"/>
            <stop offset="1" stop-color="var(--accent-light)"/>
          </linearGradient>
        </defs>
        <path d="M0 0 H230 V120 Q230 230 110 230 H0 Z" fill="url(#brandGraphicFill)"/>
      </svg>
      <div class="wordmark">
        <span class="wordmark__mark"></span>
        <span class="wordmark__name">Bramwell IT Services</span>
      </div>
      <div class="name-band">
        <h1 class="name-band__name">Marcus Tenley</h1>
      </div>
      <ul class="contacts">
        <li class="contacts__item"><span class="contacts__label">P</span><span>0483 562 904</span></li>
        <li class="contacts__item"><span class="contacts__label">E</span><span>support@bramwellit.com.au</span></li>
        <li class="contacts__item"><span class="contacts__label">W</span><span>www.bramwellit.com.au</span></li>
      </ul>
    </section>
  </main>
</body>
</html>
```